Firm Stationery Design

I need a design for stationery, including: Stationery First Page, Stationery Second Sheet, Envelope, Mailing Label for Flat Envelopes, and Business Cards

```html
<!DOCTYPE html>
<html lang="en">
<head>
<meta charset="utf-8">
<title>Marlow Law LLC – Business Cards</title>
<link rel="stylesheet" href="https://fonts.googleapis.com/css2?family=Montserrat:wght@800&family=Arimo:wght@400;700&display=swap">
<style>
  :root {
    --stage: #3b3b3d;
    --ink: #1c1c1c;
    --card-dark: #1f1f20;
    --card-dark-2: #2c2c2e;
    --paper: #ffffff;
    --accent: #f29a00;
    --muted: #3a3a3a;
    --rule: #d6d6d6;
  }
  * { box-sizing: border-box; margin: 0; padding: 0; }
  html, body { width: 1200px; height: 689px; overflow: hidden; background: var(--stage); }
  .canvas {
    position: relative; width: 1200px; height: 689px;
    display: flex; align-items: center; justify-content: center; gap: 52px;
  }
  .card {
    position: relative; width: 504px; height: 288px;
    border-radius: 16px; overflow: hidden;
  }
  /* back of card */
  .card--back {
    background: linear-gradient(135deg, var(--card-dark-2), var(--card-dark));
  }
  .card--back .texture { position: absolute; inset: 0; }
  .back-mark {
    position: absolute; left: 50%; top: 50%; transform: translate(-50%, -50%);
    display: flex; align-items: center; gap: 8px;
    background: var(--paper); padding: 10px 14px;
  }
  .back-mark .mark-name {
    font: 800 16px/1 "Montserrat", sans-serif; color: var(--ink); letter-spacing: 1px;
  }
  /* front of card */
  .card--front { background: var(--paper); }
  .card--front .band { position: absolute; inset: 0; }
  .brand {
    position: absolute; left: 92px; top: 104px;
    display: flex; align-items: flex-start; gap: 10px;
  }
  .brand-square { width: 22px; height: 22px; background: var(--accent); margin-top: 4px; }
  .brand-name {
    font: 800 26px/1.05 "Montserrat", sans-serif; color: var(--ink); letter-spacing: 1px;
  }
  .divider {
    position: absolute; left: 270px; top: 40px; width: 1px; height: 200px; background: var(--rule);
  }
  .contact {
    position: absolute; left: 290px; top: 52px; width: 200px;
    font-family: "Arimo", sans-serif; color: var(--muted);
  }
  .contact-name { font-weight: 700; font-size: 18px; color: var(--ink); letter-spacing: .3px; }
  .contact-role { font-size: 11px; color: var(--accent); margin-top: 2px; }
  .contact-address { font-size: 10.5px; line-height: 1.4; margin-top: 14px; }
  .contact-list { list-style: none; margin-top: 14px; font-size: 10.5px; line-height: 1.55; }
  .contact-list li { display: flex; align-items: center; gap: 7px; }
  .contact-list svg { width: 10px; height: 10px; flex: none; }
</style>
</head>
<body>
<main class="canvas">
  <section class="card card--back" aria-label="Business card, back">
    <div class="texture" role="img" aria-label="Tonal embossed tile pattern in dark charcoal"></div>
    <div class="back-mark">
      <span class="mark-name">MARLOW</span>
    </div>
  </section>

  <section class="card card--front" aria-label="Business card, front">
    <svg class="band" viewBox="0 0 504 288" aria-hidden="true">
      <polygon points="0,0 60,0 60,210 150,288 0,288" fill="var(--card-dark)"/>
    </svg>
    <div class="brand">
      <span class="brand-square"></span>
      <span class="brand-name">MARLOW<br>LAW LLC</span>
    </div>
    <div class="divider"></div>
    <div class="contact">
      <p class="contact-name">DANIEL REYES</p>
      <p class="contact-role">President</p>
      <p class="contact-address">412 Cedar Hollow Road<br>Halden, Canada 58210</p>
      <ul class="contact-list">
        <li><svg viewBox="0 0 10 10"><path d="M2 1l2 2-1 1.2c.6 1.2 1.6 2.2 2.8 2.8L7 6l2 2-1.5 1.5C4.5 9 1 5.5.5 2.5z" fill="var(--accent)"/></svg>555-218-4407</li>
        <li><svg viewBox="0 0 10 10"><rect x="2.5" y=".5" width="5" height="9" rx="1" fill="none" stroke="var(--accent)"/></svg>555-390-1162</li>
        <li><svg viewBox="0 0 10 10"><rect x=".5" y="2" width="9" height="6" fill="var(--accent)"/><path d="M.5 2l4.5 3.5L9.5 2" fill="none" stroke="#fff" stroke-width=".8"/></svg>hello@marlowlaw.com</li>
        <li><svg viewBox="0 0 10 10"><circle cx="5" cy="5" r="4.5" fill="var(--accent)"/></svg>www.marlowlaw.com</li>
      </ul>
    </div>
  </section>
</main>
</body>
</html>
```